Website design for legal tech start up in Switzerland (B2B)

We are for a legal tech start up in Switzerland called KOVA. We have been running since August 2016. This will be our first live website.

We need a website designed and business card design for our start-up in Switzerland. We also need the Web design to be converted into HTML and CSS files.

Function of website:
• To inform potential customers of our services
• Form a key part of our digital marketing and sales footprint.
• Branding

Please find attached logo.
Updates

Project Deadline Extended Reason: Giving us time to review submissions and provide opportunity for more submissions. Added Thursday, February 16, 2017

Project Deadline Extended
Reason: Looking for more idea's not necessarily set on blue and grey colours only.

Target Market(s)

B2B tech powered legal services.

Industry/Entity Type

Legal

Contact Information for Business Card

Lean and slick design.

Coding

Coded - Design and coding required

Number of Pages Required

5+ page

Requirements
Must have
• VERY LEAN AND CLEAN DESIGN!
• We have received many great standard designs, but we are looking for something more out-of-the box: You can get inspiration from these designs: http://www.pixelvane.com/websites/clean/
• Thanks!!
• Easy content management system
• Well structured coding for additional development
• Responsive webpage for all types of devices
• SEO optimized
• Tabs (Home, services, team, careers, blog, contact us)
• Colour scheme complementary to logo
Nice to have
• Look and Design - Approachable, High-tech, Modern
• Easy to add chat bot capability in future
Should not have
• Too busy/ too much clutter
• Not take to long to load

```html
<!DOCTYPE html>
<html lang="en">
<head>
<meta charset="utf-8">
<title>KOVA – Legal Technology</title>
<link rel="stylesheet" href="https://fonts.googleapis.com/css2?family=Arimo:ital,wght@0,400;0,700;1,400&family=Tinos:wght@400;700&display=swap">
<style>
:root{
  --navy:#1d4579;
  --navy-dark:#143560;
  --navy-deep:#0f2b52;
  --blue:#2a5ea3;
  --ink:#333;
  --ink-soft:#555;
  --logo-grey:#3b3d42;
  --line:#c9ced6;
  --paper:#fff;
  --footer-base:#1b426f;
  --copy-bar:#3a3a3a;
  --board:#4a4d50;
  --board-dark:#2a2c2f;
}
*{margin:0;padding:0;box-sizing:border-box}
html,body{width:1200px;height:2510px;overflow:hidden;background:var(--paper)}
body{position:relative;font-family:"Arimo",Arial,sans-serif;color:var(--ink)}
.abs{position:absolute}

/* header */
.brand{left:160px;top:24px;font:700 66px/1 "Arimo",Arial,sans-serif;color:var(--logo-grey);letter-spacing:4px}
.topbar{left:736px;top:0;width:464px;height:34px;background:#e6e7e9;border-bottom-left-radius:20px}
.topbar .call{position:absolute;left:24px;top:7px;font-size:13px;color:var(--ink);display:flex;align-items:center;gap:8px}
.social{display:flex;gap:6px}
.social span{width:22px;height:22px;border-radius:50%;background:var(--navy);display:block}
.topbar .social{position:absolute;left:182px;top:6px}
.cta{left:795px;top:55px;width:234px;height:40px;background:var(--navy);color:#fff;font:400 14px/40px "Tinos",serif;text-align:center;border-radius:2px;letter-spacing:.3px}
.mainnav{left:0;top:104px;width:1200px;height:43px;background:linear-gradient(#2b5a92,var(--navy-dark));border-top:1px solid #0d2646}
.mainnav a{position:absolute;top:14px;color:#fff;font:400 14px/1 "Tinos",serif;text-decoration:none}
.mainnav .follow{position:absolute;left:786px;top:14px;color:#fff;font:400 14px/1 "Tinos",serif}
.mainnav .social{position:absolute;left:898px;top:10px}
.mainnav .social span{background:transparent;border:1.5px solid #fff}

/* hero */
.hero{left:0;top:147px;width:1200px;height:503px;overflow:hidden;
  background:
    radial-gradient(ellipse 260px 200px at 150px 470px,#1c2f55 0,rgba(28,47,85,.75) 45%,rgba(28,47,85,0) 100%),
    radial-gradient(ellipse 120px 160px at 330px 350px,rgba(196,150,120,.55),rgba(196,150,120,0) 100%),
    radial-gradient(ellipse 260px 230px at 600px 270px,rgba(190,192,194,.45),rgba(190,192,194,0) 100%),
    radial-gradient(ellipse 300px 180px at 930px 230px,rgba(170,172,175,.3),rgba(170,172,175,0) 100%),
    radial-gradient(ellipse at 55% 45%,#626568,var(--board) 55%,var(--board-dark))}
.hero-caption{position:absolute;left:0;bottom:0;width:100%;height:59px;background:rgba(20,20,22,.78);color:#fff;font-size:25px;line-height:59px;text-align:center}
.hero-arrow{position:absolute;top:218px;width:22px;height:28px;background:#222;border:1px solid #666}
.hero-arrow svg{display:block;margin:8px auto}

/* titles */
.section-title{width:1200px;left:0;text-align:center;font:400 33px/1 "Tinos",serif;color:#222}
.rule{left:432px;width:336px;height:1px;background:var(--line)}
.rule::after{content:"";position:absolute;left:148px;top:-1px;width:40px;height:3px;background:var(--navy)}
.welcome-text{left:178px;top:756px;width:844px;font:400 11.6px/19.5px "Tinos",serif;color:var(--ink-soft);text-align:center}

/* services */
.services{left:0;top:905px;width:1200px;height:480px}

/* why choose */
.why{left:0;top:1397px;width:1200px;height:436px;background:linear-gradient(#1f4d86,var(--navy-deep))}
.why-title{top:47px;color:#fff;font-size:28px}
.why .rule{top:90px;background:rgba(255,255,255,.5)}
.why .rule::after{background:#fff}
.reason{position:absolute;color:#fff;font:400 12px/17px "Tinos",serif}
.reason h3{font:400 15.5px/20px "Tinos",serif;margin-bottom:2px}
.reason.r{text-align:right}
.why-logo{left:0;top:353px;width:1200px;text-align:center;font:700 64px/1 "Arimo",Arial,sans-serif;color:var(--logo-grey);letter-spacing:4px}

/* testimonials */
.testi-title{top:1904px;font-size:28px}
.testi-title b{font-weight:400;color:var(--blue)}
.quote{left:240px;top:1980px;width:720px;font:italic 400 14.5px/25px "Arimo",Arial,sans-serif;color:#444;text-align:center}
.qmark{font:700 48px/1 "Tinos",serif;color:#c8c8c8}
.author{left:0;width:1200px;text-align:center}
.dots{left:572px;top:2134px;display:flex;gap:8px}
.dots span{width:9px;height:9px;border-radius:50%;background:#bbb}
.dots span:first-child{background:var(--navy)}

/* footer */
.footer{left:0;top:2184px;width:1200px;height:280px;background:linear-gradient(100deg,var(--navy-deep),var(--footer-base) 55%,#244f84)}
.footer h4{position:absolute;font:400 18px/1 "Tinos",serif;color:#fff}
.footer .divider{position:absolute;top:50px;width:1px;height:200px;background:rgba(255,255,255,.2)}
.links{position:absolute;left:164px;top:88px;list-style:none;font:400 12.5px/21.8px "Tinos",serif;color:#fff}
.links li::before{content:"› "}
.contact{position:absolute;left:314px;color:#fff;font:400 12.5px/20px "Tinos",serif;display:flex;gap:10px}
.contact svg{flex:none;margin-top:2px}
.field{position:absolute;left:562px;width:208px;background:#fff;border-radius:2px;font-size:11px;color:#333;padding:8px 7px}
.submit{position:absolute;left:562px;top:229px;width:104px;height:32px;background:#0c0f14;color:#fff;font:700 14px/32px "Tinos",serif;padding-left:12px}
.footer .social{position:absolute;left:922px;top:87px}
.footer .social span{width:24px;height:24px;background:#fff}
.foot-logo{position:absolute;left:917px;top:158px;font:700 38px/1 "Arimo",Arial,sans-serif;color:#c9d4e3;letter-spacing:2px}
.copy{left:0;top:2464px;width:1200px;height:46px;background:var(--copy-bar);color:#ddd;font:400 12px/46px "Tinos",serif;text-align:center}
</style>
</head>
<body>

<header>
  <div class="abs brand">KOVA</div>
  <div class="abs topbar">
    <div class="call"><svg width="20" height="20" viewBox="0 0 20 20"><circle cx="10" cy="10" r="10" fill="#1d4579"/><path d="M7 5.5l2 2-1 1.3c.6 1.4 1.7 2.5 3.2 3.2l1.3-1 2 2-1.2 1.5C9.7 14.4 5.6 10.3 5.5 6.7z" fill="#fff"/></svg>Call : 123-456-7890</div>
    <div class="social" aria-label="Social links"><span></span><span></span><span></span><span></span></div>
  </div>
  <div class="abs cta">GET A FREE CONSULTATION</div>
  <nav class="abs mainnav">
    <a style="left:185px">Home</a>
    <a style="left:273px">Services</a>
    <a style="left:373px">Team</a>
    <a style="left:457px">Careers</a>
    <a style="left:552px">Blog</a>
    <a style="left:632px">Contact Us</a>
    <span class="follow">Follow Us On</span>
    <div class="social"><span></span><span></span><span></span><span></span></div>
  </nav>
</header>

<section class="abs hero" role="img" aria-label="Photo of a hand in a business shirt sketching charts and a light bulb on a chalkboard">
  <div class="hero-arrow" style="left:6px"><svg width="8" height="10" viewBox="0 0 8 10"><path d="M6 1L2 5l4 4" stroke="#fff" stroke-width="2" fill="none"/></svg></div>
  <div class="hero-arrow" style="right:6px"><svg width="8" height="10" viewBox="0 0 8 10"><path d="M2 1l4 4-4 4" stroke="#fff" stroke-width="2" fill="none"/></svg></div>
  <div class="hero-caption">Helping Technology Companies Succeed</div>
</section>

<section>
  <h1 class="abs section-title" style="top:686px">Welcome to KOVA</h1>
  <div class="abs rule" style="top:734px"></div>
  <p class="abs welcome-text">Lorem ipsum dolor sit amet, consectetuer adipiscing elit, sed diam nonummy nibh euismod tincidunt ut laoreet dolore magna aliquam erat volutpat. Ut wisi enim ad minim veniam, quis nostrud exerci tation ullamcorper suscipit lobortis nisl ut aliquip ex ea commodo consequat. Duis autem vel eum iriure dolor in hendrerit in vulputate velit esse molestie consequat, vel illum dolore eu feugiat nulla facilisis at vero eros et accu nonummy nibh euismod tincidunt ut laoreet dolore magna aliquam erat volutpat. Ut wisi enim ad minim veniam, quis nostrud exerci tation ullamcorper suscipit lobortis nisl ut aliquip ex ea commodo consequat. Duis autmean et iusto odio dignissim qui blandit praesent luptatum zzril delenit augue duis dolore te feugait nulla facilisi.</p>
</section>

<svg class="abs services" viewBox="0 0 1200 480" aria-label="Our services">
  <defs>
    <polygon id="hex" points="0,-121 106,-61 106,61 0,121 -106,61 -106,-61"/>
    <polygon id="hexin" points="0,-110 96,-55 96,55 0,110 -96,55 -96,-55"/>
    <linearGradient id="frame" x1="0" y1="0" x2="0" y2="1"><stop offset="0" stop-color="#f4f4f4"/><stop offset="1" stop-color="#cfcfcf"/></linearGradient>
    <radialGradient id="g-info" cx=".45" cy=".4" r=".75"><stop offset="0" stop-color="#eef1f4"/><stop offset=".55" stop-color="#b7c4d3"/><stop offset="1" stop-color="#5c7594"/></radialGradient>
    <radialGradient id="g-case" cx=".55" cy=".35" r=".8"><stop offset="0" stop-color="#d6dce2"/><stop offset=".5" stop-color="#7d93ad"/><stop offset="1" stop-color="#2f4d72"/></radialGradient>
    <radialGradient id="g-app" cx=".45" cy=".35" r=".8"><stop offset="0" stop-color="#5c7fa6"/><stop offset=".45" stop-color="#24395a"/><stop offset="1" stop-color="#0d1522"/></radialGradient>
    <radialGradient id="g-env" cx=".5" cy=".2" r=".9"><stop offset="0" stop-color="#e6f2c8"/><stop offset=".45" stop-color="#86b45e"/><stop offset="1" stop-color="#2c5222"/></radialGradient>
    <radialGradient id="g-word" cx=".55" cy=".55" r=".8"><stop offset="0" stop-color="#b9a88f"/><stop offset=".45" stop-color="#5d4b3e"/><stop offset="1" stop-color="#1a1512"/></radialGradient>
    <radialGradient id="g-proc" cx=".45" cy=".4" r=".8"><stop offset="0" stop-color="#f2f2f2"/><stop offset=".5" stop-color="#a7a7a7"/><stop offset="1" stop-color="#4e4e4e"/></radialGradient>
    <linearGradient id="g-navy" x1="0" y1="0" x2="0" y2="1"><stop offset="0" stop-color="#22518c"/><stop offset="1" stop-color="#173d6c"/></linearGradient>
    <linearGradient id="shade" x1="0" y1="0" x2="0" y2="1"><stop offset=".55" stop-color="#000" stop-opacity="0"/><stop offset="1" stop-color="#000" stop-opacity=".45"/></linearGradient>
  </defs>
  <style>
    .hex-frame{fill:url(#frame);stroke:#e4e4e4;stroke-width:2;stroke-linejoin:round}
    .hex-label{font:700 14.5px "Tinos",serif;fill:#fff;text-anchor:middle}
    .hex-title{font:400 40px "Tinos",serif;fill:#fff;text-anchor:middle}
  </style>
  <g transform="translate(378,124)"><use href="#hex" class="hex-frame"/><use href="#hexin" fill="url(#g-info)" role="img" aria-label="Photo of a hand reviewing charts on paper"/><use href="#hexin" fill="url(#shade)"/><text class="hex-label" y="66">Information Management</text></g>
  <g transform="translate(603,124)"><use href="#hex" class="hex-frame"/><use href="#hexin" fill="url(#g-navy)"/><text class="hex-title" y="-4">Our</text><text class="hex-title" y="38">Services</text></g>
  <g transform="translate(827,124)"><use href="#hex" class="hex-frame"/><use href="#hexin" fill="url(#g-case)" role="img" aria-label="Photo of a consultant on the phone at a desk"/><use href="#hexin" fill="url(#shade)"/><rect x="-70" y="52" width="140" height="24" fill="rgba(255,255,255,.25)"/><text class="hex-label" y="69">Case Support</text></g>
  <g transform="translate(264,325)"><use href="#hex" class="hex-frame"/><use href="#hexin" fill="url(#g-app)" role="img" aria-label="Photo of a hand touching a digital app interface"/><use href="#hexin" fill="url(#shade)"/><text class="hex-label" y="66">Application Development</text></g>
  <g transform="translate(489,325)"><use href="#hex" class="hex-frame"/><use href="#hexin" fill="url(#g-env)" role="img" aria-label="Photo of a green forest canopy"/><use href="#hexin" fill="url(#shade)"/><text class="hex-label" y="66">Environmental Litigation</text></g>
  <g transform="translate(713,325)"><use href="#hex" class="hex-frame"/><use href="#hexin" fill="url(#g-word)" role="img" aria-label="Photo of a lawyer writing at a desk"/><use href="#hexin" fill="url(#shade)"/><text class="hex-label" y="66">Legal Word Processing</text></g>
  <g transform="translate(937,325)"><use href="#hex" class="hex-frame"/><use href="#hexin" fill="url(#g-proc)" role="img" aria-label="Photo of steel ball bearings on technical drawings"/><use href="#hexin" fill="url(#shade)"/><text class="hex-label" y="66">Procurement Support</text></g>
</svg>

<section class="abs why">
  <h2 class="abs section-title why-title">Why Choose Us</h2>
  <div class="abs rule"></div>
  <svg class="abs" style="left:0;top:0" width="1200" height="436" viewBox="0 0 1200 436" aria-hidden="true">
    <g stroke="#fff" stroke-width="2">
      <line x1="559" y1="280" x2="551" y2="240"/><line x1="644" y1="281" x2="654" y2="240"/>
      <line x1="489" y1="319" x2="458" y2="287"/><line x1="712" y1="320" x2="744" y2="287"/>
      <line x1="448" y1="384" x2="410" y2="371"/><line x1="752" y1="384" x2="790" y2="371"/>
    </g>
    <circle cx="600" cy="436" r="161" fill="#fff" stroke="#2a63b0" stroke-width="7"/>
    <g fill="#fff" stroke="#2a63b0" stroke-width="2">
      <circle cx="553" cy="257" r="5"/><circle cx="651" cy="258" r="5"/><circle cx="472" cy="302" r="5"/>
      <circle cx="728" cy="303" r="5"/><circle cx="425" cy="376" r="5"/><circle cx="775" cy="376" r="5"/>
    </g>
    <g fill="#fff"><circle cx="539" cy="206" r="34"/><circle cx="666" cy="206" r="34"/><circle cx="432" cy="260" r="34"/><circle cx="770" cy="260" r="34"/><circle cx="378" cy="360" r="34"/><circle cx="820" cy="360" r="34"/></g>
    <g fill="#1d4579">
      <path d="M524 196l6 6-3 4c2 4 5 7 9 9l4-3 6 6-4 5c-11-1-22-12-23-23z"/>
      <path d="M536 190h22a4 4 0 014 4v10a4 4 0 01-4 4h-12l-6 5v-5h-4a4 4 0 01-4-4v-10a4 4 0 014-4z"/>
      <circle cx="661" cy="200" r="9"/><path d="M646 226c0-10 7-15 15-15s15 5 15 15z"/>
      <circle cx="676" cy="192" r="7"/>
      <circle cx="426" cy="266" r="10"/><circle cx="441" cy="252" r="7"/>
      <rect x="755" y="246" width="26" height="26" rx="3"/><circle cx="782" cy="272" r="9"/>
      <circle cx="378" cy="355" r="11"/><rect x="373" y="366" width="10" height="8" rx="2"/>
      <circle cx="812" cy="352" r="7"/><circle cx="828" cy="352" r="7"/><path d="M800 374c0-9 6-13 12-13s12 4 12 13zM816 374c0-9 6-13 12-13s12 4 12 13z"/>
    </g>
    <g fill="#fff">
      <rect x="544" y="197" width="3" height="3"/><rect x="549" y="197" width="3" height="3"/><rect x="554" y="197" width="3" height="3"/>
      <circle cx="426" cy="266" r="4"/><circle cx="441" cy="252" r="3"/>
      <rect x="759" y="253" width="18" height="2"/><circle cx="782" cy="272" r="6"/>
      <rect x="675" y="188" width="2" height="6"/><circle cx="676" cy="196" r="1.2"/>
    </g>
    <path d="M782 268v4h3" stroke="#1d4579" stroke-width="1.5" fill="none"/>
  </svg>
  <div class="reason r" style="right:721px;top:121px"><h3>Unbiased Recommendations</h3>Lorem ipsum dolor sit mork<br>[+]...adipiscing sed diam</div>
  <div class="reason" style="left:721px;top:121px"><h3>Expert Guidance</h3>Lorem ipsum dolor sit mork<br>adipiscing sed diam...[+]</div>
  <div class="reason r" style="right:825px;top:203px"><h3>Unparalleled<br>Service</h3>Lorem ipsum dolor sit mork<br>[+]...adipiscing sed diam</div>
  <div class="reason" style="left:825px;top:220px"><h3>Considerable Time<br>For You</h3>Lorem ipsum dolor sit mork<br>adipiscing sed diam...[+]</div>
  <div class="reason r" style="right:879px;top:333px"><h3>Superior Advice</h3>Lorem ipsum dolor sit mork<br>[+]...adipiscing sed diam</div>
  <div class="reason" style="left:879px;top:318px"><h3>Deep Legal Industry<br>Relationships</h3>Lorem ipsum dolor sit mork<br>adipiscing sed diam...[+]</div>
  <div class="abs why-logo">KOVA</div>
</section>

<section>
  <h2 class="abs section-title testi-title">Clients <b>Testimonials</b></h2>
  <div class="abs rule" style="top:1946px"></div>
  <svg class="abs" style="left:133px;top:1996px" width="28" height="52" viewBox="0 0 28 52" aria-hidden="true"><path d="M24 2L4 26l20 24" stroke="#c8c8c8" stroke-width="2" fill="none"/></svg>
  <svg class="abs" style="left:1039px;top:1996px" width="28" height="52" viewBox="0 0 28 52" aria-hidden="true"><path d="M4 2l20 24-20 24" stroke="#c8c8c8" stroke-width="2" fill="none"/></svg>
  <span class="abs qmark" style="left:192px;top:1966px">“</span>
  <p class="abs quote">Lorem ipsum dolor sit amet, consectetuer adipiscing elit, sed diam nonummy nibh euismod tinciduntol ut laoreet dolore magna aliquam erat volutpat. Ut wisi enim ad minim veniam, quis nostrud exercimori mornkle tation ullamcorper suscipit lobortis nisl ut aliquip ex ea commodo consequat.</p>
  <span class="abs qmark" style="left:772px;top:2052px">”</span>
  <div class="abs author" style="top:2070px;color:var(--blue);font-size:15px">Marla T.</div>
  <div class="abs author" style="top:2091px;color:#333;font-size:13px">Lugano, TI</div>
  <div class="abs dots"><span></span><span></span><span></span><span></span></div>
</section>

<footer class="abs footer">
  <h4 style="left:164px;top:45px">Quick Links</h4>
  <ul class="links"><li>Home</li><li>Services</li><li>Team</li><li>Careers</li><li>Blog</li><li>Contact Us</li></ul>
  <div class="divider" style="left:293px"></div>
  <h4 style="left:316px;top:45px">Contact Details</h4>
  <div class="contact" style="top:88px"><svg width="16" height="16" viewBox="0 0 16 16"><circle cx="8" cy="8" r="8" fill="#fff"/><path d="M8 3a3 3 0 013 3c0 2.5-3 6-3 6S5 8.5 5 6a3 3 0 013-3z" fill="#1b426f"/><circle cx="8" cy="6" r="1.1" fill="#fff"/></svg><div>Kova Technology<br>Street Name City Name<br>State Zipcode</div></div>
  <div class="contact" style="top:155px"><svg width="16" height="16" viewBox="0 0 16 16"><circle cx="8" cy="8" r="8" fill="#fff"/><path d="M5.5 4l1.5 1.5-.8 1c.5 1.1 1.3 1.9 2.4 2.4l1-.8 1.5 1.5-.9 1.1C7.6 10.5 4.6 7.5 4.5 5z" fill="#1b426f"/></svg><div>123-456-7890</div></div>
  <div class="contact" style="top:194px"><svg width="16" height="16" viewBox="0 0 16 16"><circle cx="8" cy="8" r="8" fill="#fff"/><path d="M5.5 4l1.5 1.5-.8 1c.5 1.1 1.3 1.9 2.4 2.4l1-.8 1.5 1.5-.9 1.1C7.6 10.5 4.6 7.5 4.5 5z" fill="#1b426f"/></svg><div>123-456-7890</div></div>
  <div class="contact" style="top:228px"><svg width="16" height="16" viewBox="0 0 16 16"><circle cx="8" cy="8" r="8" fill="#fff"/><rect x="4" y="5.5" width="8" height="5.5" fill="#1b426f"/><path d="M4 5.5l4 3 4-3" stroke="#fff" stroke-width=".9" fill="none"/></svg><div>inquiry@kovatechnology.com</div></div>
  <div class="divider" style="left:540px"></div>
  <h4 style="left:564px;top:45px">Quick Inquiry</h4>
  <div class="field" style="top:86px;height:31px">Name</div>
  <div class="field" style="top:122px;height:32px">Email</div>
  <div class="field" style="top:159px;height:62px">Message</div>
  <div class="submit">Submit <span style="margin-left:12px">→</span></div>
  <h4 style="left:932px;top:52px">Follow Us</h4>
  <div class="social"><span></span><span></span><span></span><span></span></div>
  <div class="foot-logo">KOVA</div>
</footer>
<div class="abs copy">Copyright © 2017 Kova Technology. All Rights Reserved.</div>

</body>
</html>
```